Design a Travel and Tourism website

We would like a freelancer to design a website that is essentially easy to use and navigate database providing local information for Travelers about destination countries.

We proposed website would discuss different rates, fees, visa requirement, resort locations, cheap flights, etc. This website should be elegant and modern. Our business name is rovanix.
Some reference websites are zemplorift.ca, brindlefoxhaven.com,
There should be a forum in the website where travell\ers discuss about their first hand tranvel experience to such destinations.

Tourism

```html
<!DOCTYPE html>
<html lang="en">
<head>
<meta charset="utf-8">
<title>Rovanix — find your adventure</title>
<link rel="stylesheet" href="https://fonts.googleapis.com/css2?family=Montserrat:wght@300;400;500;600;700&display=swap">
<style>
  :root {
    --ink: #565b69;
    --ink-soft: #5e6a85;
    --body-text: #6a7290;
    --muted: #a3a3ab;
    --white: #ffffff;
    --page: #ffffff;
    --arrow: #c9cbd8;
    --sky: #e7e3d8;
    --haze: #b9c2b4;
    --ridge: #5e7468;
    --slope: #3d3a3a;
    --shadow: #2b2630;
  }
  * { margin: 0; padding: 0; box-sizing: border-box; }
  html, body { width: 1200px; height: 1200px; overflow: hidden; background: var(--page); }
  body { font-family: "Montserrat", sans-serif; position: relative; }

  .hero {
    position: absolute; left: 0; top: 0; width: 1200px; height: 724px;
    background: linear-gradient(180deg, var(--sky) 0%, #e1ddd0 22%, var(--haze) 36%, var(--ridge) 50%, #4a4b45 66%, var(--slope) 80%, var(--shadow) 100%);
  }

  .brand { position: absolute; left: 60px; top: 44px; display: flex; align-items: center; gap: 12px; }
  .brand-dot { width: 40px; height: 40px; border: 3px solid var(--ink); border-radius: 50%; }
  .brand-name { font-size: 36px; font-weight: 400; color: var(--ink); letter-spacing: 1px; line-height: 1; }

  .lang { position: absolute; left: 332px; top: 68px; font-size: 12px; font-weight: 600; color: var(--ink); display: flex; align-items: center; gap: 4px; }

  .nav { position: absolute; top: 60px; font-size: 19px; color: var(--ink); }
  .menu { position: absolute; left: 1094px; top: 63px; width: 38px; }
  .menu span { display: block; height: 1.5px; background: var(--ink); margin-bottom: 9px; }

  .headline { position: absolute; left: 0; width: 1200px; top: 172px; text-align: center; font-size: 64px; font-weight: 300; color: var(--ink); letter-spacing: 3px; }

  .tabs { position: absolute; left: 66px; top: 387px; width: 196px; height: 36px; border: 1.5px solid var(--white); border-radius: 8px; display: flex; }
  .tab { font-size: 16px; font-weight: 600; color: var(--white); display: flex; align-items: center; justify-content: center; }
  .tab.active { width: 92px; background: var(--white); color: var(--ink); border-radius: 6px; }
  .tab.idle { flex: 1; }

  .field { position: absolute; top: 474px; transform: translateX(-50%); text-align: center; color: var(--white); white-space: nowrap; }
  .field-label { font-size: 13.5px; font-weight: 700; letter-spacing: .8px; }
  .field-label small { font-size: 12px; font-weight: 400; letter-spacing: 0; }
  .field-value { font-size: 15px; font-weight: 400; margin-top: 6px; display: flex; justify-content: center; align-items: center; gap: 14px; }

  .search { position: absolute; left: 974px; top: 458px; width: 160px; height: 72px; border: 2px solid var(--white); border-radius: 6px; color: var(--white); font-size: 20px; font-weight: 600; display: flex; align-items: center; justify-content: center; }

  .avatar { position: absolute; left: 562px; top: 690px; width: 76px; height: 76px; border-radius: 50%; border: 3px solid var(--white); background: radial-gradient(circle at 50% 45%, #d9a78e 0%, #a86a4c 55%, #6b3d2a 100%); }

  .author { position: absolute; left: 0; width: 1200px; top: 776px; text-align: center; font-size: 14.5px; font-weight: 600; color: var(--ink-soft); }
  .place { position: absolute; left: 0; width: 1200px; top: 812px; text-align: center; font-size: 14px; letter-spacing: 3px; color: var(--muted); }

  .story-title { position: absolute; left: 0; width: 1200px; top: 898px; text-align: center; font-size: 42px; font-weight: 300; color: var(--ink-soft); }
  .story-text { position: absolute; left: 300px; width: 600px; top: 977px; text-align: center; font-size: 16.5px; line-height: 22px; color: var(--body-text); }
  .read-more { position: absolute; left: 0; width: 1200px; top: 1044px; text-align: center; font-size: 19px; font-weight: 700; color: var(--ink-soft); }
  .read-more span { border-bottom: 1.5px solid var(--ink-soft); }

  .arrow { position: absolute; top: 942px; }
</style>
</head>
<body>
  <div class="hero" role="img" aria-label="Misty mountain range with a hiker standing on a rocky ledge"></div>

  <div class="brand"><div class="brand-dot"></div><div class="brand-name">ROVANIX</div></div>
  <div class="lang">FR
    <svg width="14" height="9" viewBox="0 0 14 9"><path d="M1 1l6 6 6-6" fill="none" stroke="#565b69" stroke-width="1.6"/></svg>
  </div>

  <div class="nav" style="left:679px">resorts</div>
  <div class="nav" style="left:766px">flights</div>
  <div class="nav" style="left:850px">fees</div>
  <div class="nav" style="left:913px">visas</div>
  <div class="nav" style="left:982px">login</div>
  <div class="menu"><span></span><span></span><span></span></div>

  <h1 class="headline">find your adventure</h1>

  <div class="tabs"><div class="tab active">flights</div><div class="tab idle">resorts</div></div>

  <div class="field" style="left:113px"><div class="field-label">FROM</div><div class="field-value">enter airport</div></div>
  <div class="field" style="left:262px"><div class="field-label">TO</div><div class="field-value">enter airport</div></div>
  <div class="field" style="left:406px"><div class="field-label">DEPART</div><div class="field-value">dd / mm / yy</div></div>
  <div class="field" style="left:554px"><div class="field-label">RETURN</div><div class="field-value">dd / mm / yy</div></div>
  <div class="field" style="left:683px"><div class="field-label">ADULTS</div><div class="field-value">1 <svg width="12" height="7" viewBox="0 0 12 7"><path d="M1 1l5 5 5-5" fill="none" stroke="#fff" stroke-width="1"/></svg></div></div>
  <div class="field" style="left:836px"><div class="field-label">CHILDREN <small>( under 17 )</small></div><div class="field-value">0 <svg width="12" height="7" viewBox="0 0 12 7"><path d="M1 1l5 5 5-5" fill="none" stroke="#fff" stroke-width="1"/></svg></div></div>

  <div class="search">search</div>

  <div class="avatar" role="img" aria-label="Profile photo of the story author"></div>
  <div class="author">by mirawen</div>
  <div class="place">SCOTLAND</div>

  <h2 class="story-title">Share Your Story</h2>
  <p class="story-text">Lorem ipsum dolor sit amet, consectetur adipisicing elit, sed do eiusmod tempor incididunt ut labore et dolore magna aliqua.</p>
  <div class="read-more"><span>Read more</span></div>

  <svg class="arrow" style="left:88px" width="50" height="88" viewBox="0 0 50 88"><path d="M46 2L4 44l42 42" fill="none" stroke="var(--arrow)" stroke-width="1.5"/></svg>
  <svg class="arrow" style="left:1060px" width="50" height="88" viewBox="0 0 50 88"><path d="M4 2l42 42L4 86" fill="none" stroke="var(--arrow)" stroke-width="1.5"/></svg>
</body>
</html>
```